BRAMBLEFORD CONSTRUCTIONS B-Card

I currently have a b-card design but will be removing the image (tree) from the logo and have text only.
I want the card to be classy and strong within the building and construction industry.
I will be using Spot UV on the cards as per the attached examples. I will also send through some sketched ideas that I have in mind.
The color blue is similar to the image (No. 6) attached images

Target Market(s)

middle to maturre aged.
Home Owners / Renovators and Builders

Industry/Entity Type

Construction

Contact Information for Business Card

BRAMBLEFORD CONSTRUCTIONS
Name: Gareth Pennick
Title: Project Manager
Mobile: 0427 351 804
Office: (08) 9316 5172
Address: 47C Corvell Street, Malaga WA 6090
Email: info@bramblefordhomes.com.au
PO Box: 3817 Malaga WA 6944

Colors
0592cd
33a6d7
85cae6
1b1b1b

Requirements
Must have
• 1. It must have spot UV on the front of card, maybe back of card too
• 2. I really like the blue on image 6. (or at least a really cool electric blue against the charcoal grey background)
• 3. The font must be slimline and modern. Easy to read
• 4. There must be no black used on the card... Only greys and dark charcoal greys
• 5. Use only the text from the logo "Brambleford Constructions" Not the image of the tree. I am wanting the b-cards to be more masculine.
Nice to have
• 1. I like the design concept on image 6. but happy to see what else you can do with the Spot UV
• 2. Unless you have a really cool idea of the image of the tree (from previous logo) Spot UV somewhere in the design concept thats original and different then I am keen to see what you come up with
• 3. Try changing the color of the logo eg. full white or Blue and white
• 4. Another option is to have the Brambleford Logo on the front of card with the spot UV in the background of text which we specialise in eg, Roofing, Ceiling, Insulation, Gutter Guards, Electrical, Insurance etc and we can add or reduce items as required. Similar to image 12.
Should not have
• Do not include the image of the tree from previous logo. unless you have a really cool idea of Spot UV somewhere in the design concept thats original and different.

```html
<!DOCTYPE html>
<html lang="en">
<head>
<meta charset="utf-8">
<title>Brambleford Constructions – Business Card</title>
<link rel="stylesheet" href="https://fonts.googleapis.com/css2?family=Source+Sans+3:wght@400;600;700&display=swap">
<style>
  :root {
    --page: #e9e9ea;
    --charcoal: #2a2a2c;
    --charcoal-deep: #222224;
    --pattern-tone: #333336;
    --blue: #33a6d7;
    --blue-bright: #0592cd;
    --silver: #d9d9db;
    --white: #ffffff;
    --text-light: #f2f2f2;
  }
  * { box-sizing: border-box; margin: 0; padding: 0; }
  html, body {
    width: 1200px; height: 900px; overflow: hidden;
    background: var(--page);
    font-family: "Source Sans 3", "Segoe UI", sans-serif;
  }
  .sheet {
    width: 1200px; height: 900px;
    display: flex; flex-direction: column; align-items: center; justify-content: center;
    gap: 40px;
  }
  .card {
    position: relative;
    width: 680px; height: 389px;
    background: var(--charcoal);
    overflow: hidden;
    box-shadow: 0 6px 18px rgba(40, 40, 44, 0.25);
  }

  /* Front */
  .card-front__pattern {
    position: absolute; inset: 0;
    background: radial-gradient(ellipse at 50% 50%, var(--pattern-tone) 0%, var(--charcoal-deep) 100%);
  }
  .wordmark {
    position: absolute;
    font-weight: 600;
    line-height: 1;
    text-transform: uppercase;
  }
  .wordmark__name { display: block; }
  .wordmark__sub { display: block; }
  .card-front .wordmark {
    left: 78px; top: 150px;
    color: var(--white);
  }
  .card-front .wordmark__name { font-size: 56px; letter-spacing: 1px; }
  .card-front .wordmark__sub { font-size: 22px; letter-spacing: 14.5px; margin-top: 8px; padding-left: 4px; }

  /* Back */
  .card-back .wordmark {
    right: 40px; top: 58px;
    color: var(--blue);
    text-align: left;
  }
  .card-back .wordmark__name { font-size: 30px; letter-spacing: 0.5px; }
  .card-back .wordmark__sub { font-size: 12px; letter-spacing: 7.6px; margin-top: 4px; padding-left: 2px; }

  .card-back__wave { position: absolute; inset: 0; }

  .contact {
    position: absolute; left: 52px; top: 92px;
    color: var(--text-light);
  }
  .contact__name { font-size: 21px; font-weight: 700; color: var(--blue); }
  .contact__title { font-size: 15px; font-weight: 600; margin-top: 0px; }
  .contact__phones { list-style: none; margin-top: 34px; font-size: 16px; line-height: 1.4; }
  .contact__phones li { display: flex; align-items: center; gap: 10px; }
  .contact__phones svg { width: 12px; height: 14px; flex: none; }
  .contact__address { font-style: normal; margin-top: 28px; font-size: 16px; line-height: 1.35; padding-left: 22px; }
</style>
</head>
<body>
<main class="sheet">

  <section class="card card-front" aria-label="Business card front">
    <div class="card-front__pattern" role="img" aria-label="Repeating spot UV tree pattern across the dark charcoal background"></div>
    <div class="wordmark">
      <span class="wordmark__name">Brambleford</span>
      <span class="wordmark__sub">Constructions</span>
    </div>
  </section>

  <section class="card card-back" aria-label="Business card back">
    <svg class="card-back__wave" viewBox="0 0 680 389" preserveAspectRatio="none" aria-hidden="true">
      <path d="M0 318 C 150 372, 300 345, 420 275 C 470 245, 500 228, 520 222 C 470 262, 420 300, 360 330 C 250 385, 110 380, 0 345 Z" fill="var(--silver)"/>
      <path d="M0 346 C 130 385, 280 378, 400 318 C 500 268, 580 200, 680 168 L 680 389 L 0 389 Z" fill="var(--blue)"/>
    </svg>

    <div class="wordmark">
      <span class="wordmark__name">Brambleford</span>
      <span class="wordmark__sub">Constructions</span>
    </div>

    <div class="contact">
      <p class="contact__name">Gareth Pennick</p>
      <p class="contact__title">Project Manager</p>
      <ul class="contact__phones">
        <li>
          <svg viewBox="0 0 12 14" aria-hidden="true"><rect x="2.5" y="0.8" width="7" height="12.4" rx="1.4" fill="none" stroke="var(--blue)" stroke-width="1.4"/><circle cx="6" cy="11" r="0.8" fill="var(--blue)"/></svg>
          <span>0427 351 804</span>
        </li>
        <li>
          <svg viewBox="0 0 12 14" aria-hidden="true"><path d="M1 5 Q6 1 11 5 L10 6.5 L8 6 L7.6 4.6 Q6 4.2 4.4 4.6 L4 6 L2 6.5 Z" fill="var(--blue)"/><rect x="2.5" y="7.5" width="7" height="5" rx="1" fill="var(--blue)"/></svg>
          <span>(08) 9316 5172</span>
        </li>
      </ul>
      <address class="contact__address">
        47C Corvell Street, Malaga WA 6090<br>
        PO Box: 3817 Malaga WA 6944
      </address>
    </div>
  </section>

</main>
</body>
</html>
```